New Business Card for Odd Fern Designs

I create and make jewellery and Clothing. But when it comes to business card design I fail completely.

Sketching is my area, drawing, putting things together neatly, not so much.

Here is a little blurb about my company:

Odd Fern Designs is a truly unique customer experience. Work one on one with Owner Petra Wolcott to make your costuming dreams come true.

Not after a costume? Browse through the store for a look at beautiful and unique piece of jewellery. Each piece has been put together by Petra, by hand. You'll find Steampunk, gothic, lolita and other quirky styles.

Want something else? What abotu a pair of warm kitty paws? A Pair of Kitty ears? A pony tail to wear on your jeans? There are so many options and things to choose! You will want to take it all home.

I have attached the previous business card with my mascot "Greta" As you can see there is a very Greta in Cloudmere feel to the overall company, with references to The Tin Tinker, and the idea that "We are all made here".

Colour's to use would be purple and blue. The winning design would show the unique but professional approach that Odd Fern Designs takes when creating each piece for their customers.

Reason: Wanted to give you a chance to go over feed back that has been sent out. I am committed to paying for the design that I will use. I think another week will help tweak things up.

Target Market(s)

Nerds, Geeks and Sci-Fi people aged 20 - 34 both Male and Female

Industry/Entity Type

Store

Requirements
Must have
• Website address: www.oddferndesigns.example

Yeah, rest is up too you!
Nice to have
• Honestly, if you could make the whole thing look like a Edwin Marlowe "Greta in Cloudmere" Drawing with the same line working style that would be amazing!

But I won't restrict you! I'd like to see what you can come up with.

```html
<!DOCTYPE html>
<html lang="en">
<head>
<meta charset="utf-8">
<title>Odd Fern Designs – Business Card</title>
<link rel="stylesheet" href="https://fonts.googleapis.com/css2?family=Lobster&family=Archivo+Narrow:wght@700&display=swap">
<style>
  :root {
    --page: #ffffff;
    --teal: #00adbf;
    --mist: #dcdde1;
    --plum: #8e3c94;
    --plum-back: #8d3e93;
    --ink-brown: #7a5821;
    --gold: #efb54b;
    --orange: #f3991f;
  }
  html, body {
    margin: 0;
    padding: 0;
    width: 1200px;
    height: 1032px;
    overflow: hidden;
    background: var(--page);
  }
  .canvas {
    position: relative;
    width: 1200px;
    height: 1032px;
  }
  .card {
    position: absolute;
    width: 464px;
    height: 803px;
  }
  .card--front {
    left: 113px;
    top: 113px;
    background: linear-gradient(to bottom,
      var(--teal) 0%,
      var(--teal) 18%,
      #7cc6cf 40%,
      var(--mist) 62%,
      #d3c6d6 75%,
      #ad7fb2 90%,
      var(--plum) 100%);
    overflow: hidden;
  }
  .card--front::before,
  .card--front::after {
    content: "";
    position: absolute;
    top: 0;
    bottom: 0;
    width: 62px;
    background: linear-gradient(to bottom, rgba(0,60,80,0.08), rgba(60,40,70,0.06));
  }
  .card--front::before { left: 0; }
  .card--front::after { right: 0; }
  .card--back {
    left: 622px;
    top: 116px;
    background: var(--plum-back);
  }
  .details {
    position: absolute;
    left: 70px;
    top: 202px;
    width: 324px;
    text-align: center;
  }
  .owner-name {
    margin: 0;
    font-family: "Lobster", cursive;
    font-size: 38px;
    line-height: 46px;
    color: var(--ink-brown);
  }
  .owner-email {
    margin: 0 0 2px;
    font-family: "Archivo Narrow", "Arial Narrow", sans-serif;
    font-weight: 700;
    font-size: 23px;
    line-height: 34px;
    color: var(--ink-brown);
  }
  .tagline {
    margin: 0;
    font-family: "Lobster", cursive;
    font-size: 47px;
    line-height: 58px;
    color: var(--gold);
  }
  .website {
    margin: 4px 0 0;
    font-family: "Lobster", cursive;
    font-size: 25px;
    line-height: 34px;
    color: var(--orange);
  }
  .mascot {
    position: absolute;
    left: 98px;
    top: 525px;
    width: 272px;
    height: 228px;
  }
</style>
</head>
<body>
  <main class="canvas">
    <section class="card card--front" aria-label="Business card front">
      <div class="details">
        <p class="owner-name">Petra Wolcott</p>
        <p class="owner-email">hello@oddferndesigns.example</p>
        <p class="tagline">Handcrafted<br>flighs of fancy</p>
        <p class="website">www.oddferndesigns.example</p>
      </div>
      <svg class="mascot" viewBox="0 0 272 228" role="img" aria-label="Ink illustration of the mascot Greta in a top hat, sitting and leaning back">
        <defs>
          <linearGradient id="mascot-tone" x1="0" y1="0" x2="0" y2="1">
            <stop offset="0" stop-color="#8a8590" stop-opacity="0.45"/>
            <stop offset="1" stop-color="#7d5a86" stop-opacity="0.45"/>
          </linearGradient>
        </defs>
        <rect x="0" y="0" width="272" height="228" rx="18" fill="url(#mascot-tone)"/>
      </svg>
    </section>
    <section class="card card--back" aria-label="Business card back"></section>
  </main>
</body>
</html>
```